Recruitment of Archipel Manpower for the UK market

I want a website for the UK market to attract businesses and companies to come to us for Philipine labour. We want an information site that gives all information on what we do and how we can recruit Philippine labour.
This is a recruitment site for companies to contact us with their requirements for skilled workers coming from the Philipines over to the UK to work.

Target Market(s)

Uk Companies and businesses who want Philipine skilled workers

Industry/Entity Type

REcruitment

Coding

Number of Pages Required

5+ page

Font styles to use
Sans Serif

Colors
0054AA
0677BA
7BADD7
CADEEF
E8F1F8
0094D4
00A9DD
6FCCEA
C7EBF8
E9F6FB
EE7325
F08F49
F5BC92
FAE3D3
FDF4ED
EB3D1F
EC4F4E
F09395
F8D3D4
FCEDEE

Requirements
Must have
• Look professional and corperate with drop down menus for Home ,about, services,articles. training , contact us
Nice to have
• Look at Velmora recruitment- https://velmorarecruitment.example.co.uk/. This is my current site - https://www.trellanstaffing.example.com/
Should not have
• Cartoons or silly pictures , needs to be corperate looking

```html
<!DOCTYPE html>
<html lang="en">
<head>
<meta charset="utf-8">
<title>Archipel Manpower – Skilled Philippine Workers for UK Companies</title>
<link href="https://fonts.googleapis.com/css2?family=Roboto:wght@400;500;700&family=Roboto+Condensed:ital,wght@1,700&display=swap" rel="stylesheet">
<style>
:root{
  --blue:#0054AA;
  --blue-bright:#0677BA;
  --sky:#0094D4;
  --red:#EB3D1F;
  --ink:#111;
  --text:#555;
  --grey-bg:#f5f6f8;
  --navy:#12294a;
  --white:#fff;
}
*{box-sizing:border-box;margin:0;padding:0}
html,body{width:1200px;height:5038px;overflow:hidden}
body{font-family:"Roboto",sans-serif;color:var(--text);background:var(--white);position:relative}
.abs{position:absolute}
.display{font-family:"Roboto Condensed","Roboto",sans-serif;font-style:italic;font-weight:700;color:var(--ink)}
.accent-red{color:var(--red)}
.accent-blue{color:var(--sky)}
.btn{display:inline-flex;align-items:center;gap:8px;border-radius:24px;font-size:14px;font-weight:500;color:#fff;height:44px;padding:0 26px}
.btn svg{width:16px;height:10px}
.btn-red{background:var(--red)}
.btn-blue{background:var(--blue)}
.photo{border:0}

/* header */
.site-header{top:0;left:0;width:1200px;height:90px;background:#fff}
.brand{left:52px;top:22px;font-size:26px;font-weight:700;color:#8b2230;display:flex;align-items:center;gap:10px}
.brand i{display:block;width:22px;height:22px;background:#8b2230}
.main-nav{left:382px;top:36px;display:flex;gap:26px;font-size:12.5px;color:#333;letter-spacing:.3px}
.main-nav .active{color:var(--blue-bright)}
.phone-tab{right:0;top:0;width:290px;height:90px;background:var(--red);clip-path:polygon(28px 0,100% 0,100% 100%,0 100%);display:flex;align-items:center;justify-content:center;gap:10px;color:#fff;font-size:25px;font-weight:500}

/* hero */
.hero{top:90px;left:0;width:1200px;height:577px;background:linear-gradient(100deg,#3b4048 0%,#6b6a62 45%,#9a8a6a 70%,#5e5a54 100%)}
.hero-copy{left:124px;top:195px}
.hero-title{font-size:38px;line-height:46px;color:#fff;padding-left:14px;border-left:4px solid var(--red)}
.hero-sub{margin-top:10px;color:#fff;font-size:15px;line-height:25px;width:450px}
.hero-copy .btn{margin-top:24px}
.contact-card{left:738px;top:172px;width:338px;height:412px;background:#fff;padding:26px 30px}
.contact-card h2{font-size:28px;text-align:center;margin-bottom:20px}
.field{height:40px;border:1px solid #ddd;border-radius:4px;margin-bottom:13px;display:flex;align-items:center;gap:8px;padding:0 12px;font-size:12px;color:#888;font-style:italic}
.field.msg{height:78px;align-items:flex-start;padding-top:10px}
.field svg{width:12px;height:12px;fill:#bbb}
.contact-card .btn{margin-top:2px;font-size:14px}

/* about */
.about{top:667px;left:0;width:1200px;height:613px}
.dots{background-image:radial-gradient(#d9dde3 1.2px,transparent 1.3px);background-size:8px 8px}
.eyebrow{font-size:12px;letter-spacing:5px;color:#444}
.sec-title{font-size:34px}
.rule{width:46px;height:2px;background:var(--blue)}
.about-text{left:660px;top:105px;width:378px}
.about-text .sec-title{margin-top:8px}
.about-text .rule{margin:12px 0 24px}
.about-text p{font-size:12px;line-height:23px;margin-bottom:12px}
.about-text .btn{margin-top:8px;height:40px;padding:0 24px}

/* working together */
.work{top:1280px;left:0;width:1200px;height:2110px;background:var(--grey-bg)}
.center-head{width:1200px;text-align:center;left:0}
.center-head .rule{margin:10px auto 22px}
.center-head p{font-size:15px;color:#222}
.step-text{width:340px}
.step-head{display:flex;align-items:center;gap:14px}
.step-num{width:42px;height:42px;border-radius:50%;background:var(--blue);color:#fff;font-weight:700;font-size:22px;display:flex;align-items:center;justify-content:center}
.step-head h3{font-size:26px}
.step-text p{margin:14px 0 0 58px;font-size:12px;line-height:23px;text-align:justify}
.frame{border-top:7px solid var(--red)}
.frame-r{border-right:7px solid var(--red)}
.frame-l{border-left:7px solid var(--red)}

/* centers */
.centers{top:3390px;left:0;width:1200px;height:775px;background:#fff}

/* services */
.services{top:4165px;left:0;width:1200px;height:515px;background:#fff}
.card{width:278px;height:330px;background:#fff;box-shadow:0 4px 18px rgba(0,0,0,.08)}
.card-top{display:flex;align-items:center;height:88px}
.card-icon{width:88px;height:88px;background:var(--blue);display:flex;align-items:center;justify-content:center}
.card-icon svg{width:44px;height:44px;stroke:#fff;fill:none;stroke-width:2}
.card h3{font-size:27px;line-height:31px;padding-left:14px}
.card p{font-size:12px;line-height:22px;padding:16px 26px 0;text-align:justify}
.card .more{display:block;padding:14px 26px 0;color:var(--red);font-size:13px;font-weight:700}

/* footer */
.site-footer{top:4680px;left:0;width:1200px;height:305px;background:linear-gradient(180deg,#1a3152,#0f2340)}
.footer-brand{left:165px;top:80px;font-size:28px;font-weight:700;color:#fff;display:flex;align-items:center;gap:10px}
.footer-brand i{display:block;width:22px;height:22px;background:#fff}
.socials{left:220px;top:172px;display:flex;gap:12px}
.socials span{width:34px;height:34px;border-radius:50%;border:2px solid #fff;background:var(--blue)}
.f-col h4{font-size:17px;color:#fff;font-weight:700;margin-bottom:22px}
.f-col a{display:block;font-size:13px;color:#fff;line-height:27px}
.f-col a.current{color:var(--sky)}
.f-row{display:flex;gap:12px;color:#fff;font-size:13px;line-height:21px;margin-bottom:12px}
.f-row svg{width:16px;height:16px;flex:none;margin-top:2px;fill:var(--sky)}
.copyright{top:4985px;left:0;width:1200px;height:53px;background:var(--red);color:#fff;font-size:13px;display:flex;align-items:center;justify-content:center}
</style>
</head>
<body>

<header class="site-header abs">
  <div class="brand abs"><i></i>Archipel Manpower</div>
  <nav class="main-nav abs">
    <span class="active">HOME</span><span>ABOUT</span><span>SERVICES ⌄</span><span>ARTICLES</span><span>TRAINING</span><span>CONTACT US</span>
  </nav>
  <div class="phone-tab abs">
    <svg width="26" height="26" viewBox="0 0 24 24" fill="#fff"><path d="M6.6 10.8a15.1 15.1 0 006.6 6.6l2.2-2.2a1 1 0 011-.25 11.4 11.4 0 003.6.57 1 1 0 011 1V20a1 1 0 01-1 1A17 17 0 013 4a1 1 0 011-1h3.5a1 1 0 011 1c0 1.25.2 2.45.57 3.57a1 1 0 01-.25 1z"/></svg>
    078 5521 0394
  </div>
</header>

<section class="hero abs" role="img" aria-label="Smiling engineers in hard hats and safety vests on a work site">
  <div class="hero-copy abs">
    <h1 class="hero-title display">Recruiting And Placing<br><span class="accent-blue">Skilled Philippine Workers</span><br>Into UK Companies</h1>
    <p class="hero-sub">We source skilled workers directly from the Philippines to work in the UK.</p>
    <span class="btn btn-red">CONTACT US <svg viewBox="0 0 16 10"><path d="M0 5h14M10 1l4 4-4 4" stroke="#fff" fill="none" stroke-width="1.6"/></svg></span>
  </div>
</section>
<form class="contact-card abs">
  <h2 class="display">Contact Us Today</h2>
  <div class="field"><svg viewBox="0 0 12 12"><circle cx="6" cy="3.5" r="3"/><path d="M0 12a6 5 0 0112 0z"/></svg>Name</div>
  <div class="field"><svg viewBox="0 0 12 12"><rect x="0" y="2" width="12" height="8"/></svg>Email</div>
  <div class="field"><svg viewBox="0 0 24 24"><path d="M6.6 10.8a15.1 15.1 0 006.6 6.6l2.2-2.2a1 1 0 011-.25 11.4 11.4 0 003.6.57 1 1 0 011 1V20a1 1 0 01-1 1A17 17 0 013 4a1 1 0 011-1h3.5a1 1 0 011 1c0 1.25.2 2.45.57 3.57a1 1 0 01-.25 1z"/></svg>Phone</div>
  <div class="field msg"><svg viewBox="0 0 12 12"><path d="M9 0l3 3-7 7H2V7z"/></svg>Message</div>
  <span class="btn btn-blue">Send Message <svg viewBox="0 0 16 10"><path d="M0 5h14M10 1l4 4-4 4" stroke="#fff" fill="none" stroke-width="1.6"/></svg></span>
</form>

<section class="about abs">
  <div class="abs dots" style="left:128px;top:88px;width:200px;height:180px"></div>
  <div class="abs dots" style="left:440px;top:410px;width:140px;height:110px"></div>
  <div class="abs photo" role="img" aria-label="Smiling workers in hard hats holding a tablet" style="left:160px;top:120px;width:226px;height:246px;background:linear-gradient(135deg,#d9c7b3,#8aa0b8)"></div>
  <div class="abs photo" role="img" aria-label="Group of smiling care workers in blue uniforms" style="left:404px;top:90px;width:192px;height:198px;background:linear-gradient(135deg,#8fb4d6,#c4a48c)"></div>
  <div class="abs photo" role="img" aria-label="Engineers in white hard hats reviewing equipment" style="left:338px;top:306px;width:180px;height:180px;background:linear-gradient(135deg,#9a9fa6,#c9504a)"></div>
  <div class="abs photo" role="img" aria-label="Medical team of doctors and nurses" style="left:178px;top:384px;width:142px;height:142px;background:linear-gradient(135deg,#eef2f6,#7ea6c9)"></div>
  <div class="about-text abs">
    <div class="eyebrow">ABOUT</div>
    <h2 class="sec-title display">Archipel <span class="accent-red">Manpower</span></h2>
    <div class="rule"></div>
    <p>We source skilled workers directly from the Philippines to work in the UK. With offices , training locations and specialist recruiters we can find the highest quality individuals to add value and resources to any UK buisness. We delivery quality based on vast experience over a number of years.</p>
    <p>Our company has been estabilished in the Philippines for <b>over 20 years.</b> We have mainly been recruiting philippine workers for the off shore industry in asia but since brexit and the new rules on skilled workers entering the UK we have been working with UK companies.</p>
    <span class="btn btn-blue">Read More <svg viewBox="0 0 16 10"><path d="M0 5h14M10 1l4 4-4 4" stroke="#fff" fill="none" stroke-width="1.6"/></svg></span>
  </div>
</section>

<section class="work abs">
  <div class="center-head abs" style="top:72px">
    <div class="eyebrow">WORKING TOGETHER</div>
    <h2 class="sec-title display" style="margin-top:8px">Archipel Manpower <span class="accent-red">Recruit</span></h2>
    <div class="rule"></div>
    <p>We recruit the finest talent available with our dedicated 200 strong team.</p>
  </div>

  <div class="step-text abs" style="left:160px;top:292px">
    <div class="step-head"><span class="step-num">1</span><h3 class="display">What We Do</h3></div>
    <p>Our company has been estabilished in the Philippines for <b>over 20 years.</b> We have mainly been recruiting philippine workers for the off shore industry in asia but since brexit and the new rules on skilled workers entering the UK we have been working with UK companies who now have chance to recruit some of the finest hard working talent from the Philippines for their companies.</p>
  </div>
  <div class="abs dots" style="left:580px;top:420px;width:120px;height:170px"></div>
  <div class="abs frame frame-r" style="left:828px;top:230px;width:210px;height:170px"></div>
  <div class="abs photo" role="img" aria-label="Recruiter selecting from a network of candidate profiles" style="left:611px;top:238px;width:420px;height:342px;background:linear-gradient(135deg,#e6e8ea,#b8624e 60%,#cfd5da)"></div>

  <div class="abs frame frame-l" style="left:162px;top:702px;width:210px;height:170px"></div>
  <div class="abs dots" style="left:500px;top:900px;width:130px;height:130px"></div>
  <div class="abs photo" role="img" aria-label="Passport visa pages with an approved work permit stamp" style="left:169px;top:708px;width:420px;height:342px;background:linear-gradient(135deg,#cfd6c7,#9fb3c4 55%,#ecebe6)"></div>
  <div class="step-text abs" style="left:640px;top:765px;width:400px">
    <div class="step-head"><span class="step-num">2</span><h3 class="display">How We Help</h3></div>
    <p>We work with companies to find skilled workers that meet the UK requirements for Visas and work permits. We guide you through the whole process and deliver highly trained people that add value to your business. We are here to help both the companies and the Philippino people to gain a better standard of living for their families.</p>
  </div>

  <div class="step-text abs" style="left:160px;top:1185px">
    <div class="step-head"><span class="step-num">3</span><h3 class="display">Where To Start</h3></div>
    <p>We need to know what your issues are and how we can understand the personnal you require , over what time frame and the number of employees you need. Once this is established we start sourcing workers in the Philippines that meet your criteria while starting the process in the UK to be able to have all the documents in place to deliver your company hard working skilled individuals.</p>
  </div>
  <div class="abs dots" style="left:580px;top:1320px;width:120px;height:160px"></div>
  <div class="abs frame frame-r" style="left:828px;top:1167px;width:210px;height:170px"></div>
  <div class="abs photo" role="img" aria-label="Two businessmen discussing a document at a desk" style="left:611px;top:1175px;width:420px;height:342px;background:linear-gradient(135deg,#c9ccd0,#3f4c5e 55%,#e3e5e8)"></div>

  <div class="abs frame frame-l" style="left:162px;top:1637px;width:210px;height:170px"></div>
  <div class="abs photo" role="img" aria-label="Smiling businessman shaking hands across a desk" style="left:169px;top:1643px;width:420px;height:342px;background:linear-gradient(135deg,#6e5c50,#d9dbdd 55%,#3a4656)"></div>
  <div class="step-text abs" style="left:640px;top:1700px;width:400px">
    <div class="step-head"><span class="step-num">4</span><h3 class="display">Contact Us Today</h3></div>
    <p>Please contact us today with your requirements , this can be care workers ,chef, welders, pipe fitters, caravan cabinet makers, medical workers. The UK list of required skills is extensive and the Philippines offerseng lish speaking highly qualified hard working employees. Contact us today and make that first step to a highly motivated , quality skilled workforce.</p>
  </div>
</section>

<section class="centers abs">
  <div class="center-head abs" style="top:78px">
    <div class="eyebrow">CENTERS</div>
    <h2 class="sec-title display" style="margin-top:8px">Archipel Manpower <span class="accent-red">Centers</span></h2>
    <div class="rule"></div>
    <p>Our centres are highlighted in red dots on the map.</p>
  </div>
  <div class="abs" role="img" aria-label="Map of the Philippines with red dots marking centres in Baguio, Manila, Batangas, Bacolod and Davao" style="left:445px;top:200px;width:310px;height:490px;border-radius:40% 30% 45% 35%;background:radial-gradient(ellipse at 50% 50%,#e4ecf5 0%,#f3f7fb 60%,#fff 100%)"></div>
</section>

<section class="services abs">
  <article class="card abs" style="left:160px;top:90px">
    <div class="card-top"><div class="card-icon"><svg viewBox="0 0 44 44"><rect x="10" y="6" width="24" height="32" rx="2"/><path d="M16 16h12M16 23h12M16 30h8"/></svg></div><h3 class="display">UK Skilled<br>Workers List</h3></div>
    <p>The UK government since brexit have developed a new system based on points (similar to Australia) when recruiting from outside of the UK. Previously EU citizens could work in the UK without any extensive documentation or clarification...</p>
    <span class="more">Read More →</span>
  </article>
  <article class="card abs" style="left:460px;top:90px">
    <div class="card-top"><div class="card-icon"><svg viewBox="0 0 44 44"><rect x="8" y="8" width="28" height="28" rx="2"/><circle cx="17" cy="18" r="4"/><path d="M24 16h8M24 22h8M14 30h18"/></svg></div><h3 class="display">Sponsor<br>Licence</h3></div>
    <p>If you have areas of your business that meet the entry requirements of skilled labour your next step is to gain a sponsor licence for your business. There are different types of licences depending on the size of the business.</p>
    <span class="more">Read More →</span>
  </article>
  <article class="card abs" style="left:760px;top:90px">
    <div class="card-top"><div class="card-icon"><svg viewBox="0 0 44 44"><circle cx="26" cy="22" r="11"/><path d="M26 15v7l5 3M6 36h20M10 36V24"/></svg></div><h3 class="display">Recruitment<br>Timeline</h3></div>
    <p>Brief us on the job profiles – this is passed on to our teams in the Philippines.<br>• Our teams in the Philippines source suitable candidates, documentation required for each candidate will be checked and vetted by the...</p>
    <span class="more">Read More →</span>
  </article>
</section>

<footer class="site-footer abs">
  <div class="footer-brand abs"><i></i>Archipel Manpower</div>
  <div class="socials abs" aria-label="Social media links"><span></span><span></span><span></span><span></span></div>
  <div class="f-col abs" style="left:556px;top:70px">
    <h4>Quick Links</h4>
    <a class="current">Home</a><a>About</a><a>Services</a><a>Articles</a><a>Training</a><a>Contact Us</a>
  </div>
  <div class="f-col abs" style="left:756px;top:70px;width:300px">
    <h4>Contact Details</h4>
    <div class="f-row"><svg viewBox="0 0 24 24"><path d="M12 2a7 7 0 00-7 7c0 5 7 13 7 13s7-8 7-13a7 7 0 00-7-7zm0 9.5A2.5 2.5 0 1112 6.5a2.5 2.5 0 010 5z"/></svg><div><b>ARCHIPEL MANPOWER</b><br>Orchard Row, Harlow Bay<br>HX9 4 United Kingdom</div></div>
    <div class="f-row"><svg viewBox="0 0 24 24"><path d="M6.6 10.8a15.1 15.1 0 006.6 6.6l2.2-2.2a1 1 0 011-.25 11.4 11.4 0 003.6.57 1 1 0 011 1V20a1 1 0 01-1 1A17 17 0 013 4a1 1 0 011-1h3.5a1 1 0 011 1c0 1.25.2 2.45.57 3.57a1 1 0 01-.25 1z"/></svg><b>078 5521 0394</b></div>
    <div class="f-row"><svg viewBox="0 0 24 24"><path d="M2 5h20v14H2zm2 2v.5l8 5 8-5V7z"/></svg>sales@archipelmanpower.example.com</div>
  </div>
</footer>
<div class="copyright abs">© 2023 Archipel Manpower Ltd. All Rights Reserved.</div>

</body>
</html>
```